Custom Manufacturing Company square space website design

I own a custom manufacturing company that uses precision cutting technology to manufacture project components over a couple industries. We have an industrial CNC router and state of the art edge bander and cut a lot of cabinetry components for cabinet shops, builders, closet companies, ect. We offer design and assembly for any cabinetry or can build cabinets to spec. We also cut components for other industries out of wood, plastics, acryclics, ect. We offer design engineering services, product development protype services. we have a 3D printer farm. We want our communicate trust, dependability, and the value we place on client relationships.

We essentially want a credibility website. Landing page and drops downs for services we offer, capabilites, about us, contact

```html
<!DOCTYPE html>
<html lang="en">
<head>
<meta charset="utf-8">
<title>Northfield Cut Works</title>
<link rel="stylesheet" href="https://fonts.googleapis.com/css2?family=Michroma&family=Figtree:wght@400;500;600;700&display=swap">
<style>
:root{
  --ink:#1e1e1e;
  --text:#4a4a4a;
  --muted:#6b6b6b;
  --white:#ffffff;
  --light:#f0f0f0;
  --line:#d8d8d8;
  --dark:#2e3337;
  --darkline:#8a8f93;
  --wood1:#6b4a2e;
  --wood2:#b07a4a;
}
*{margin:0;padding:0;box-sizing:border-box}
html,body{width:1200px;height:3735px;overflow:hidden}
body{position:relative;background:var(--white);font-family:"Figtree",sans-serif;color:var(--text)}
.abs{position:absolute}
.display{font-family:"Michroma",sans-serif;color:var(--ink);letter-spacing:5px;line-height:1;white-space:nowrap}
.btn{position:absolute;border:2px solid var(--ink);font-family:"Michroma",sans-serif;font-size:9px;letter-spacing:1.5px;line-height:1;white-space:nowrap;color:var(--ink);display:flex;align-items:center;justify-content:center}
.photo{position:absolute}
.brand-name{font-family:"Figtree",sans-serif;font-weight:700;color:var(--ink);letter-spacing:2px}

/* header */
.topbar{left:355px;top:0;width:845px;height:29px;background:var(--ink);clip-path:polygon(0 0,100% 0,100% 100%,20px 100%);color:var(--white);font-size:12px;white-space:nowrap;display:flex;align-items:center;gap:14px;padding-left:48px}
.topbar .soc{display:flex;gap:6px;margin-left:30px}
.topbar .soc span{width:20px;height:20px;border-radius:50%;background:var(--white)}
.logo{left:120px;top:22px;display:flex;align-items:center;gap:10px}
.logo .mark{width:26px;height:26px;border:2px solid var(--ink)}
.logo .brand-name{font-size:17px;line-height:1.1}
.nav{top:66px;font-size:15px;color:var(--text);white-space:nowrap}

/* hero */
.hero{left:0;top:123px;width:1200px;height:599px;background:linear-gradient(180deg,#2b2b2b 0%,#4a4642 40%,var(--wood1) 55%,var(--wood2) 65%,#5a5550 78%,#d8d6d2 100%)}
.hero-panel{left:615px;top:262px;width:585px;height:198px;background:rgba(30,30,30,.45)}
.hero-title{right:120px;top:162px;font-size:42px;color:var(--white);text-align:right;letter-spacing:6px}
.hero-sub{right:120px;top:218px;font-size:30px;color:var(--white);text-align:right;letter-spacing:4px}
.hero-rule{left:540px;top:234px;width:225px;height:2px;background:var(--white)}
.hero-text{left:648px;top:288px;width:420px;color:var(--white);font-size:15px;line-height:27px}
.hero-btn{border-color:var(--white);color:var(--white)}

/* about */
.h2{font-size:24px}
.h2-rule{height:2px;background:var(--ink)}
.p{font-size:15px;line-height:25.7px;color:var(--text)}

/* services */
.services{left:0;top:1355px;width:1200px;height:763px;background:var(--light)}
.card{background:var(--white);box-shadow:0 2px 6px rgba(0,0,0,.08)}
.card-title{font-size:18px;font-weight:600;color:var(--ink);text-align:center;line-height:29px}
.card-text{font-size:15px;line-height:26px;text-align:center;color:var(--text)}

/* contact */
.contact{left:0;top:2787px;width:1200px;height:572px;background:var(--dark)}
.contact-title{color:var(--white)}
.field-label{font-size:12px;color:var(--white)}
.field-line{height:1px;background:var(--darkline)}
.icon-box{width:61px;height:55px;border-radius:12px;background:#eef0f2;display:flex;align-items:center;justify-content:center}

/* footer */
.foot-h{font-family:"Michroma",sans-serif;font-size:13px;letter-spacing:3px;color:var(--ink);white-space:nowrap}
.foot-link{font-size:15px;color:var(--text)}
.foot-soc{width:38px;height:38px;border-radius:50%;background:var(--ink)}
</style>
</head>
<body>

<!-- Header -->
<div class="abs topbar">
  <span>✉ info@northfieldcutworks.com</span><span>|</span>
  <span>Call Us : +1 (555) 010 2040</span><span>|</span>
  <span>Client Help Center</span>
  <div class="soc"><span></span><span></span><span></span><span></span></div>
</div>
<div class="abs logo"><div class="mark"></div><div class="brand-name">NORTHFIELD<br>CUT WORKS</div></div>
<div class="abs nav" style="left:385px">Home</div>
<div class="abs nav" style="left:459px">Services we offer</div>
<div class="abs nav" style="left:610px">Capabilities</div>
<div class="abs nav" style="left:727px">About Us</div>
<div class="abs nav" style="left:824px">Contact</div>
<div class="btn" style="left:920px;top:55px;width:168px;height:46px">REQUEST A QUOTE</div>

<!-- Hero -->
<div class="abs hero" role="img" aria-label="Modern kitchen with wood cabinetry, dark dining chairs and a concrete wall"></div>
<div class="abs hero-panel"></div>
<div class="abs display hero-title">NORTHFIELD</div>
<div class="abs display hero-sub">CUT WORKS</div>
<div class="abs hero-rule"></div>
<div class="abs hero-text">precision cutting technology to manufacture project components over a couple industries</div>
<div class="btn hero-btn" style="left:649px;top:370px;width:168px;height:46px">REQUEST A QUOTE</div>

<!-- About -->
<div class="abs" style="left:109px;top:875px;width:80px;height:258px;border:3px solid var(--ink);border-right:none"></div>
<div class="abs" style="left:364px;top:810px;width:158px;height:128px;border:3px solid var(--ink);border-left:none"></div>
<div class="abs" style="left:364px;top:810px;width:3px;height:30px;background:var(--ink)"></div>
<div class="photo" style="left:188px;top:840px;width:310px;height:247px;background:linear-gradient(180deg,#d9d4cc,#b9a080 60%,#8e7050)" role="img" aria-label="Kitchen cabinetry under construction"></div>
<div class="photo" style="left:136px;top:1052px;width:206px;height:203px;background:linear-gradient(135deg,#e9dcc6,#c99a5e 60%,#8a6238)" role="img" aria-label="Woodworker assembling furniture in a workshop"></div>
<div class="photo" style="left:364px;top:1107px;width:163px;height:149px;background:linear-gradient(180deg,#3a3430,#a67d56 70%,#6e4e34)" role="img" aria-label="Finished dark kitchen interior"></div>

<div class="abs display h2" style="left:604px;top:828px">ABOUT US</div>
<div class="abs h2-rule" style="left:604px;top:862px;width:200px"></div>
<p class="abs p" style="left:604px;top:887px;width:487px">Lorem ipsum dolor sit amet, consectetur adipiscing elit, sed do eiusmod tempor incididunt ut labore et dolore magna aliqua. Ut enim ad minim veniam, quis nostrud exercitation ullamco laboris nisi ut aliquip ex ea commodo consequat. Duis aute irure dolor in reprehenderit in voluptate velit esse cillum dolore eu fugiat nulla pariatur. Excepteur sint occaecat cupidatat non proident, sunt in culpa qui officia deserunt mollit anim id est laborum.</p>
<p class="abs p" style="left:604px;top:1085px;width:487px">Lorem ipsum dolor sit amet, consectetur adipiscing elit, sed do eiusmod tempor incididunt ut labore et dolore magna aliqua. Ut enim ad minim veniam, quis nostrud exercitation ullamco laboris nisi ut aliquip ex ea commodo consequat.</p>
<div class="btn" style="left:604px;top:1224px;width:126px;height:46px">READ MORE</div>

<!-- Services -->
<div class="abs services"></div>
<div class="abs display h2" style="left:0;width:1200px;text-align:center;top:1434px">OUR SERVICES</div>
<p class="abs p" style="left:200px;width:800px;top:1495px;text-align:center">Sed ut perspiciatis unde omnis iste natus error sit voluptatem accusantium doloremque laudantium, totam rem aperiam, eaque ipsa quae ab illo inventore veritatis archite vitae dicta sunt explicabo.</p>
<svg class="abs" style="left:917px;top:1550px" width="192" height="154" aria-hidden="true">
  <defs><pattern id="dots" width="9" height="9" patternUnits="userSpaceOnUse"><circle cx="2" cy="2" r="1.4" fill="#555"/></pattern></defs>
  <rect width="192" height="40" fill="url(#dots)"/><rect x="165" y="40" width="27" height="114" fill="url(#dots)"/>
</svg>

<div class="abs card" style="left:113px;top:1655px;width:307px;height:345px"></div>
<div class="photo" style="left:120px;top:1587px;width:290px;height:234px;background:linear-gradient(180deg,#8a7a5e,#c0a06a 50%,#4e5560)" role="img" aria-label="Engineers reviewing plans on a factory floor"></div>
<div class="abs card" style="left:448px;top:1655px;width:307px;height:381px;box-shadow:0 8px 0 #d6d6d6"></div>
<div class="photo" style="left:454px;top:1587px;width:290px;height:234px;background:linear-gradient(180deg,#3a2c24,#b5683a 55%,#6c4028)" role="img" aria-label="Rows of product prototypes in a digital warehouse"></div>
<div class="abs card" style="left:781px;top:1655px;width:307px;height:345px"></div>
<div class="photo" style="left:787px;top:1587px;width:290px;height:234px;background:linear-gradient(180deg,#5a5a5e,#8a8a90 50%,#c65a3a)" role="img" aria-label="Rows of 3D printers in a print farm"></div>

<svg class="abs" style="left:217px;top:1775px" width="96" height="104" aria-hidden="true"><polygon points="48,3 92,28 92,76 48,101 4,76 4,28" fill="#fff" stroke="#d0d0d0" stroke-width="5"/><circle cx="48" cy="52" r="16" fill="none" stroke="#444" stroke-width="2"/><circle cx="48" cy="52" r="6" fill="none" stroke="#444" stroke-width="2"/></svg>
<svg class="abs" style="left:552px;top:1775px" width="96" height="104" aria-hidden="true"><polygon points="48,3 92,28 92,76 48,101 4,76 4,28" fill="#fff" stroke="#d0d0d0" stroke-width="5"/><circle cx="48" cy="52" r="20" fill="none" stroke="#444" stroke-width="2" stroke-dasharray="6 3"/><rect x="40" y="44" width="16" height="16" fill="none" stroke="#444" stroke-width="2"/></svg>
<svg class="abs" style="left:886px;top:1775px" width="96" height="104" aria-hidden="true"><polygon points="48,3 92,28 92,76 48,101 4,76 4,28" fill="#fff" stroke="#d0d0d0" stroke-width="5"/><rect x="30" y="34" width="36" height="38" fill="none" stroke="#444" stroke-width="2"/><line x1="30" y1="44" x2="66" y2="44" stroke="#444" stroke-width="2"/><path d="M44 44 v12 l4 4 l4 -4 v-12" fill="none" stroke="#444" stroke-width="2"/></svg>

<div class="abs card-title" style="left:113px;width:307px;top:1890px">Engineering Services</div>
<p class="abs card-text" style="left:135px;width:263px;top:1927px">Sed ut perspiciatis unde omnis iste natus error sit voluptatem</p>
<div class="abs card-title" style="left:448px;width:307px;top:1890px">Product Development<br>Prototype Services</div>
<p class="abs card-text" style="left:470px;width:263px;top:1957px">Sed ut perspiciatis unde omnis iste natus error sit voluptatem</p>
<div class="abs card-title" style="left:781px;width:307px;top:1890px">3D Printer Farm</div>
<p class="abs card-text" style="left:803px;width:263px;top:1927px">Sed ut perspiciatis unde omnis iste natus error sit voluptatem</p>

<!-- Capabilities -->
<div class="abs display h2" style="left:113px;top:2225px">OUR CAPABILITIES</div>
<div class="abs h2-rule" style="left:113px;top:2260px;width:364px"></div>
<p class="abs p" style="left:112px;top:2287px;width:450px">Lorem ipsum dolor sit amet, consectetur adipiscing elit, sed do eiusmod tempor incididunt ut labore et dolore magna aliqua. Ut enim ad minim veniam, quis nostrud exercitation ullamco laboris nisi ut aliquip ex ea commodo consequat. Duis aute irure dolor in reprehenderit in voluptate velit esse cillum dolore eu fugiat nulla pariatur. Excepteur sint occaecat cupidatat non proident, sunt in culpa qui officia deserunt mollit anim id est laborum.</p>
<p class="abs p" style="left:112px;top:2485px;width:450px">Lorem ipsum dolor sit amet, consectetur adipiscing elit, sed do eiusmod tempor incididunt ut labore et dolore magna aliqua. Ut enim ad minim veniam, quis nostrud exercitation ullamco laboris nisi ut aliquip ex ea commodo consequat.</p>
<div class="btn" style="left:112px;top:2623px;width:134px;height:46px">LEARN MORE</div>
<div class="abs" style="left:733px;top:2229px;width:467px;height:470px;background:#e4e4e4"></div>
<div class="photo" style="left:622px;top:2308px;width:527px;height:393px;background:linear-gradient(135deg,#b08850,#d8b37a 45%,#3a3a3a 75%,#c9a46c)" role="img" aria-label="Craftsman drilling a plywood cabinet box in a workshop"></div>

<!-- Contact -->
<div class="abs contact"></div>
<div class="abs" style="left:116px;top:2896px;font-size:14px;letter-spacing:2px;color:var(--darkline)">GET IN TOUCH</div>
<div class="abs display contact-title" style="left:116px;top:2932px;font-size:21px">CONTACT US</div>
<div class="abs" style="left:116px;top:2964px;width:200px;height:2px;background:var(--white)"></div>
<p class="abs" style="left:116px;top:2992px;width:380px;font-size:14px;line-height:23px;color:#c8ccd0">Lorem ipsum dolor sit amet, consectetur adipiscing elit sed do eiusmod tempor labore et dolore magna</p>
<div class="abs icon-box" style="left:116px;top:3069px"><svg width="26" height="20" aria-hidden="true"><rect x="1" y="1" width="24" height="18" rx="2" fill="none" stroke="#333" stroke-width="1.6"/><path d="M1 2 L13 11 L25 2" fill="none" stroke="#333" stroke-width="1.6"/></svg></div>
<div class="abs" style="left:198px;top:3073px;font-size:12px;color:#c8ccd0">Email address</div>
<div class="abs" style="left:198px;top:3093px;font-size:16px;font-weight:600;color:var(--white)">hello@northfieldcutworks.com</div>
<div class="abs icon-box" style="left:116px;top:3154px"><svg width="28" height="28" viewBox="0 0 24 24" aria-hidden="true"><path d="M6 3 l3 0 l2 5 l-2 2 a11 11 0 0 0 5 5 l2 -2 l5 2 l0 3 a2 2 0 0 1 -2 2 A17 17 0 0 1 4 5 a2 2 0 0 1 2 -2z" fill="none" stroke="#333" stroke-width="1.4"/></svg></div>
<div class="abs" style="left:198px;top:3156px;font-size:12px;color:#c8ccd0">Phone Number</div>
<div class="abs" style="left:198px;top:3175px;font-size:16px;font-weight:600;color:var(--white)">(555) 010 7890</div>

<div class="abs" style="left:620px;top:2856px;width:470px;height:422px;border:1.5px solid var(--darkline);border-radius:18px"></div>
<div class="abs field-label" style="left:667px;top:2904px">Name*</div><div class="abs field-line" style="left:667px;top:2933px;width:357px"></div>
<div class="abs field-label" style="left:667px;top:2961px">Email address*</div><div class="abs field-line" style="left:667px;top:2995px;width:357px"></div>
<div class="abs field-label" style="left:667px;top:3017px">Phone Number*</div><div class="abs field-line" style="left:667px;top:3050px;width:357px"></div>
<div class="abs field-label" style="left:667px;top:3072px">Message</div><div class="abs field-line" style="left:667px;top:3167px;width:357px"></div>
<div class="abs" style="left:669px;top:3188px;width:176px;height:43px;border-radius:22px;background:var(--white);display:flex;align-items:center;justify-content:center;font-size:13px;font-weight:600;color:var(--ink)">Send Message ›</div>

<!-- Footer -->
<div class="abs" style="left:116px;top:3488px;width:242px;text-align:center;display:flex;flex-direction:column;align-items:center;gap:14px">
  <div style="width:60px;height:60px;border:3px solid var(--ink)"></div>
  <div class="brand-name" style="font-size:22px;line-height:1.15">NORTHFIELD<br>CUT WORKS</div>
</div>
<div class="abs foot-h" style="left:443px;top:3488px">NAVIGATION</div>
<div class="abs foot-link" style="left:443px;top:3518px">Our apps</div>
<div class="abs foot-link" style="left:443px;top:3551px">Team</div>
<div class="abs foot-link" style="left:443px;top:3584px">Contact</div>
<div class="abs foot-h" style="left:646px;top:3488px">OUR LOCATION</div>
<svg class="abs" style="left:640px;top:3528px" width="26" height="30" viewBox="0 0 24 28" aria-hidden="true"><path d="M12 26 C4 16 3 13 3 10 a9 9 0 0 1 18 0 c0 3 -1 6 -9 16z" fill="none" stroke="#555" stroke-width="1.6"/><circle cx="12" cy="10" r="3.2" fill="none" stroke="#555" stroke-width="1.6"/></svg>
<p class="abs" style="left:675px;top:3523px;width:175px;font-size:14px;line-height:21px;color:var(--muted)">Lorem ipsum dolor sit amet, consectetu adipiscing</p>
<div class="abs foot-h" style="left:904px;top:3488px">FOLLOW US</div>
<div class="abs foot-soc" style="left:900px;top:3517px"></div>
<div class="abs foot-soc" style="left:947px;top:3517px"></div>
<div class="abs foot-soc" style="left:995px;top:3517px"></div>
<div class="abs foot-soc" style="left:1043px;top:3517px"></div>
<div class="abs" style="left:400px;width:400px;text-align:center;top:3651px;font-size:14px;color:var(--muted)">© 2023 Company Name | All Rights Reserved</div>
<div class="abs" style="left:400px;width:400px;text-align:center;top:3685px;font-size:14px;color:var(--muted)">Privacy Policy &nbsp;&nbsp;&nbsp;&nbsp; Terms of Use</div>

</body>
</html>
```